Card Design for my dog training business Brightpaw Obedience

Need a business card design for my dog training business with my new logo. Want the card to come off professional yet fun. Want it to be very eye catchy as well. I normally have these at vet clinics, pet stores, and groomers. so need it to look better than my competitors.
Target Market(s)
dog owners
Industry/Entity Type
Dog Training
Contact Information for Business Card
needs logo, my name and info
Font styles to use
Serif
Colors
0255a3
ffffff
ec1f27
000000
333333
fbfbfb
Requirements
Must have
- Brightpaw Obedience
- Felix Orland
- 415 903 2276
- info@brightpawobedience.example
- www.brightpawobedience.example

```html
<!DOCTYPE html>
<html lang="en">
<head>
<meta charset="utf-8">
<title>Brightpaw Obedience — Business Card</title>
<link rel="stylesheet" href="https://fonts.googleapis.com/css2?family=Roboto:wght@400;700&family=EB+Garamond:ital,wght@0,500;1,400&display=swap">
<style>
  :root {
    --ink: #231f20;
    --paper: #ffffff;
    --backdrop: #e4e4e4;
    --sans: "Roboto", Arial, sans-serif;
    --serif: "EB Garamond", Georgia, serif;
  }
  * { box-sizing: border-box; margin: 0; padding: 0; }
  html, body {
    width: 1125px; height: 1200px; overflow: hidden;
    background: var(--backdrop);
  }
  .card {
    position: absolute;
    left: 171px;
    width: 800px; height: 455px;
    transform: scale(1.0325);
    transform-origin: top left;
    overflow: hidden;
  }
  .card--front { top: 107px; background: var(--paper); }
  .card--back { top: 639px; background: var(--ink); }

  .front-swoosh { position: absolute; inset: 0; width: 800px; height: 455px; }

  .brand {
    position: absolute;
    font-family: var(--serif);
    font-weight: 500;
    line-height: 1.05;
    display: flex; align-items: center; gap: 12px;
  }
  .brand__dot {
    width: 18px; height: 18px; border-radius: 50%;
    flex: none;
  }
  .card--front .brand { left: 60px; top: 155px; color: var(--ink); font-size: 40px; }
  .card--front .brand__dot { background: var(--ink); }
  .card--back .brand {
    left: 0; right: 0; top: 182px; justify-content: center;
    color: var(--paper); font-size: 56px;
  }
  .card--back .brand__dot { background: var(--paper); width: 22px; height: 22px; }

  .holder {
    position: absolute; right: 38px; top: 296px;
    font-family: var(--sans); font-weight: 700; font-size: 27px;
    color: var(--paper);
  }
  .contact-list {
    position: absolute; right: 38px; top: 350px;
    list-style: none;
    font-family: var(--sans); font-size: 16.5px; color: var(--paper);
  }
  .contact-list li {
    display: flex; justify-content: flex-end; align-items: center;
    gap: 10px; height: 25.5px;
  }
  .contact-list svg { width: 16px; height: 16px; fill: var(--paper); }

  .tagline {
    position: absolute; left: 0; right: 0; top: 392px;
    text-align: center;
    font-family: var(--serif); font-style: italic; font-size: 21px;
    color: var(--paper);
  }
</style>
</head>
<body>

<section class="card card--front" aria-label="Card front">
  <svg class="front-swoosh" viewBox="0 0 800 455" aria-hidden="true">
    <path d="M342 455 Q470 175 800 132 L800 455 Z" fill="var(--ink)"/>
    <path d="M356 455 Q480 193 800 152" fill="none" stroke="var(--paper)" stroke-width="3"/>
  </svg>

  <div class="brand"><span class="brand__dot"></span><span>Brightpaw<br>Obedience</span></div>

  <h1 class="holder">Felix Orland</h1>
  <ul class="contact-list">
    <li>415 903 2276
      <svg viewBox="0 0 24 24"><path d="M6.6 10.8a15.1 15.1 0 0 0 6.6 6.6l2.2-2.2a1 1 0 0 1 1-.25 11.4 11.4 0 0 0 3.6.57 1 1 0 0 1 1 1V20a1 1 0 0 1-1 1A17 17 0 0 1 3 4a1 1 0 0 1 1-1h3.5a1 1 0 0 1 1 1c0 1.250.2 2.450.57 3.6a1 1 0 0 1-.25 1z"/></svg>
    </li>
    <li>info@brightpawobedience.example
      <svg viewBox="0 0 24 24"><path d="M3 5h18v14H3z"/><path d="M4 6.5 12 12.5 20 6.5" fill="none" stroke="var(--ink)" stroke-width="1.6"/></svg>
    </li>
    <li>www.brightpawobedience.example
      <svg viewBox="0 0 24 24"><circle cx="12" cy="12" r="10"/><path d="M7 8c2 0 3 1 3 3s-2 2-2 4M14 5c0 2 2 2 3 3s0 3 2 4" fill="none" stroke="var(--ink)" stroke-width="1.8"/></svg>
    </li>
  </ul>
</section>

<section class="card card--back" aria-label="Card back">
  <div class="brand"><span class="brand__dot"></span><span>Brightpaw Obedience</span></div>
  <p class="tagline">“Good manners start with one patient lesson.”</p>
</section>

</body>
</html>
```